Upmarket Dessert Lounge needs a Business Card Design

We are an upmarket dessert lounge needing a business card to match our image.

We want something that is simple yet beautiful, feminine, classy, sophisticated and elegant. We want it to stand out and don't mind if it is bold.

The design should include our logo and colours of red or maroon with gold highlights. We don't mind if black is used.

Marlow & Quince

Target Market(s)

For those who like to indulge or treat themselves and give in to their temptations on good quality desserts.

Industry/Entity Type

Business

Requirements
Must have
• Must include our logo and our name

Marlow & Quince

M & Q

```html
<!DOCTYPE html>
<html lang="en">
<head>
<meta charset="utf-8">
<title>Marlow &amp; Quince — Business Card</title>
<link rel="stylesheet" href="https://fonts.googleapis.com/css2?family=Open+Sans:wght@400;600&display=swap">
<style>
  :root {
    --stage: #d9d6d2;
    --card: #231b19;
    --maroon: #7e1a1c;
    --maroon-deep: #5c1012;
    --gold: #e6c27e;
    --ivory: #f4eee6;
  }
  * { box-sizing: border-box; margin: 0; padding: 0; }
  html, body { width: 1200px; height: 951px; overflow: hidden; }
  body {
    background: var(--stage);
    font-family: "Open Sans", sans-serif;
    position: relative;
  }
  .card {
    position: absolute;
    left: 250px;
    width: 700px;
    height: 400px;
    background: var(--card);
    border-radius: 22px;
    overflow: hidden;
    box-shadow: 0 10px 28px rgba(0,0,0,.25);
  }
  .card--front { top: 40px; }
  .card--back { top: 511px; }

  .edge {
    position: absolute;
    top: 0; bottom: 0;
    width: 16px;
    background: linear-gradient(90deg, var(--maroon-deep), var(--maroon), var(--maroon-deep));
  }
  .edge--left { left: 0; }
  .edge--right { right: 0; }
  .edge-tab {
    position: absolute;
    right: 0;
    top: 150px;
    width: 12px;
    height: 100px;
    background: linear-gradient(90deg, var(--maroon-deep), var(--maroon));
  }

  .brand {
    display: flex;
    align-items: center;
    gap: 16px;
    color: var(--gold);
    font-weight: 600;
  }
  .brand-dot {
    border-radius: 50%;
    background: var(--maroon);
    flex: none;
  }
  .card--front .brand {
    position: absolute;
    top: 120px;
    left: 0; right: 0;
    justify-content: center;
    font-size: 40px;
    letter-spacing: 1px;
  }
  .card--front .brand-dot { width: 34px; height: 34px; }

  .web {
    position: absolute;
    top: 290px;
    left: 0; right: 0;
    text-align: center;
    color: var(--gold);
    font-size: 17px;
    letter-spacing: 2.5px;
  }

  .card--back .brand {
    position: absolute;
    left: 50px;
    top: 160px;
    font-size: 54px;
    letter-spacing: 1px;
  }
  .card--back .brand-dot { width: 30px; height: 30px; }

  .contact {
    position: absolute;
    right: 54px;
    top: 112px;
    text-align: right;
    color: var(--ivory);
    font-size: 16px;
    line-height: 1.3;
  }
  .contact-name {
    color: var(--gold);
    font-size: 25px;
    margin-bottom: 14px;
  }
  .contact-name .amp { color: var(--ivory); }
  .contact-address { margin-bottom: 18px; }
  .contact .domain { color: var(--gold); }
</style>
</head>
<body>
  <section class="card card--front" aria-label="Business card front">
    <div class="edge edge--left"></div>
    <div class="edge edge--right"></div>
    <div class="brand">
      <span class="brand-dot"></span>
      <span class="brand-name">Marlow &amp; Quince</span>
    </div>
    <p class="web">www.marlow&amp;quince.com</p>
  </section>

  <section class="card card--back" aria-label="Business card back">
    <div class="edge-tab"></div>
    <div class="brand">
      <span class="brand-dot"></span>
      <span class="brand-monogram">M &amp; Q</span>
    </div>
    <div class="contact">
      <p class="contact-name">Marlow <span class="amp">&amp;</span> Quince</p>
      <p class="contact-address">84 Larkspur Avenue, Suite 210<br>New York, New York 10023</p>
      <p class="contact-phone">212-555-0148</p>
      <p class="contact-email">info@<span class="domain">marlow&amp;quince.com</span></p>
    </div>
  </section>
</body>
</html>
```